I need to create a product box

I need a designer for a candle-making kit. Attached please find the die-cut and some of the elements I will like to include in the box. Also, there is a sample box. I want the designer to know this is an ecofriendly product but the packaging needs to be classy, unisex and eye-catching.

file:///C:/Users/mauro/Downloads/Untitled%20design.svg

Colors
0054AA
0677BA
7BADD7
CADEEF
E8F1F8
0094D4
00A9DD
6FCCEA
C7EBF8
E9F6FB
00AB8E
00BBA5
67D7C9
C6EFE9
E9F9F6
FFF300
FFF600
FEFA6F
FFFEC7
FFFEE8
FFC000
F8CF3A
FAE287
FDF2CF
FEFAEE
F0912C
F2A743
F7CA91
FBE8D2
FDF5EE
A7469A
B969AE
D3A5CF
EDDBEB
F8F0F9

```html
<!DOCTYPE html>
<html lang="en">
<head>
<meta charset="utf-8">
<title>Wick Haven — Candle Making Kit Dieline</title>
<link href="https://fonts.googleapis.com/css2?family=EB+Garamond:ital,wght@0,400;0,500;1,400&display=swap" rel="stylesheet">
<style>
  :root {
    --navy: #121c63;
    --navy-deep: #0d1650;
    --orange: #ef7d1a;
    --orange-dark: #c4621a;
    --die-red: #d3202c;
    --ink-light: #ffffff;
    --grey: #8a8a8a;
    --page: #ffffff;
  }
  html, body {
    margin: 0;
    padding: 0;
    width: 716px;
    height: 1200px;
    overflow: hidden;
    background: var(--page);
  }
  .canvas {
    position: relative;
    width: 716px;
    height: 1200px;
    font-family: "EB Garamond", Georgia, serif;
  }
  .brand-mark {
    position: absolute;
    top: 120px;
    left: 0;
    width: 716px;
    text-align: center;
    color: var(--grey);
  }
  .brand-mark__dot {
    display: block;
    width: 22px;
    height: 22px;
    margin: 0 auto 10px;
    border-radius: 50%;
    background: var(--grey);
  }
  .brand-mark__name {
    font-size: 46px;
    font-weight: 400;
    letter-spacing: 1px;
    line-height: 1;
  }
  .brand-mark__tag {
    margin-top: 8px;
    font-size: 10px;
    letter-spacing: 3px;
    text-transform: uppercase;
  }
  .dieline {
    position: absolute;
    top: 370px;
    left: 8px;
    width: 700px;
    height: 656px;
  }
  .panel { fill: var(--navy); }
  .cut { fill: none; stroke: var(--die-red); stroke-width: 1.6; }
  .fold { stroke: var(--die-red); stroke-width: 1.2; }
  .pattern-area { fill: url(#patternTone); }
  .frame { fill: var(--navy-deep); stroke: var(--orange); stroke-width: 5; }
  .badge { fill: none; stroke: var(--ink-light); stroke-width: 3; }
  .t-white { fill: var(--ink-light); font-family: "EB Garamond", Georgia, serif; }
  .t-orange { fill: var(--orange); font-family: "EB Garamond", Georgia, serif; }
  .t-brand { font-size: 34px; font-weight: 400; }
  .t-tag { font-size: 6.5px; letter-spacing: 2px; }
  .t-tagline { font-size: 27px; font-style: italic; }
  .t-quote { font-size: 15px; font-style: italic; }
  .t-title { font-size: 25px; letter-spacing: 1.5px; }
  .t-sub { font-size: 8px; letter-spacing: 3px; }
  .t-web { font-size: 8px; letter-spacing: 1px; }
  .t-side { font-size: 20px; }
  .t-head { font-size: 9px; font-weight: 500; }
  .t-small { font-size: 7px; font-style: italic; }
  .t-fine { font-size: 5.6px; }
</style>
</head>
<body>
<main class="canvas">

  <header class="brand-mark">
    <span class="brand-mark__dot"></span>
    <div class="brand-mark__name">Wick Haven</div>
    <div class="brand-mark__tag">Luxury candle making kit</div>
  </header>

  <svg class="dieline" viewBox="60 1120 1365 1280" xmlns="http://www.w3.org/2000/svg" aria-label="Flat dieline of the candle making kit box">
    <defs>
      <linearGradient id="patternTone" x1="0" y1="0" x2="1" y2="1">
        <stop offset="0" stop-color="#d9701c"/>
        <stop offset="1" stop-color="#b95a1e"/>
      </linearGradient>
    </defs>

    <!-- top flap -->
    <g class="top-flap">
      <rect class="panel" x="390" y="1133" width="705" height="222"/>
      <rect class="cut" x="390" y="1133" width="705" height="222"/>
      <line class="fold" x1="523" y1="1133" x2="523" y2="1355"/>
      <line class="fold" x1="962" y1="1133" x2="962" y2="1355"/>
      <circle cx="744" cy="1222" r="9" fill="var(--ink-light)"/>
      <text class="t-white t-tagline" x="742" y="1268" text-anchor="middle">Let Your Creativity Shine Bright</text>
    </g>

    <!-- middle row: side walls and base -->
    <g class="middle-row">
      <rect class="panel" x="62" y="1470" width="10" height="65"/>
      <rect class="panel" x="1413" y="1470" width="9" height="65"/>
      <rect class="panel" x="70" y="1355" width="1345" height="290"/>
      <rect class="cut" x="70" y="1355" width="1345" height="290"/>
      <line class="fold" x1="297" y1="1355" x2="297" y2="1645"/>
      <line class="fold" x1="1187" y1="1355" x2="1187" y2="1645"/>

      <g class="side-info" transform="rotate(90 440 1500)">
        <text class="t-white t-side" x="440" y="1492" text-anchor="middle">Made in China</text>
        <text class="t-white t-side" x="440" y="1516" text-anchor="middle" font-size="16">SKU Number: SKU 1234</text>
      </g>

      <g class="base-panel">
        <rect class="pattern-area" x="523" y="1355" width="439" height="290" role="img" aria-label="Orange geometric lattice pattern with small candelabra motifs"/>
        <rect class="frame" x="548" y="1378" width="387" height="242"/>
        <g transform="rotate(180 741.5 1499)">
          <text class="t-orange t-head" x="566" y="1398">WARNING:</text>
          <text class="t-white t-fine" x="566" y="1409">
            <tspan x="566" dy="0">Keep away from children and pets. Never leave</tspan>
            <tspan x="566" dy="8">a burning candle unattended. Burn on a heat</tspan>
            <tspan x="566" dy="8">safe surface away from drafts.</tspan>
          </text>
          <line x1="566" y1="1440" x2="770" y2="1440" stroke="var(--ink-light)" stroke-width="0.6"/>
          <text class="t-orange t-head" x="566" y="1458">AVERTISSEMENT:</text>
          <text class="t-white t-fine" x="566" y="1469">
            <tspan x="566" dy="0">Gardez hors de portée des enfants. Ne laissez</tspan>
            <tspan x="566" dy="8">jamais une bougie allumée sans surveillance.</tspan>
            <tspan x="566" dy="8">Posez sur une surface stable.</tspan>
          </text>
          <line x1="566" y1="1500" x2="770" y2="1500" stroke="var(--ink-light)" stroke-width="0.6"/>
          <text class="t-orange t-head" x="566" y="1518">WARNING:</text>
          <text class="t-white t-fine" x="566" y="1529">
            <tspan x="566" dy="0">Hot wax can burn skin. Melt wax slowly</tspan>
            <tspan x="566" dy="8">and use the thermometer provided.</tspan>
          </text>
          <text class="t-white t-head" x="566" y="1604" font-weight="400">MADE IN CHINA</text>

          <text class="t-orange t-head" x="790" y="1398">DIY CANDLE SET:</text>
          <text class="t-white t-small" x="790" y="1412">
            <tspan x="790" dy="0">• 7*8 ounce Soy wax</tspan>
            <tspan x="790" dy="12">• 4 Glass Jars 7cm*8cm</tspan>
            <tspan x="790" dy="12">• 3*8 ounce Black Tin Cans</tspan>
            <tspan x="790" dy="12">• 20 Labels</tspan>
            <tspan x="790" dy="12">• 3 bags of Dry flowers Rose,</tspan>
            <tspan x="796" dy="12">Lavender, Fragrans.</tspan>
            <tspan x="790" dy="12">• 10 colour blocks</tspan>
            <tspan x="790" dy="12">• 10 Glue dots</tspan>
            <tspan x="790" dy="12">• 2 Gift tables</tspan>
            <tspan x="790" dy="12">• 3*Centering devices</tspan>
            <tspan x="790" dy="12">• 7*10ml fragrance oil</tspan>
            <tspan x="790" dy="12">• One Digital thermometer</tspan>
            <tspan x="790" dy="12">• One Mixing spoon</tspan>
            <tspan x="790" dy="12">• 10 candle wicks</tspan>
            <tspan x="790" dy="12">• One customized carton</tspan>
          </text>
        </g>
      </g>

      <g class="side-badges">
        <circle class="badge" cx="1062" cy="1418" r="21"/>
        <circle class="badge" cx="1062" cy="1474" r="21"/>
        <circle class="badge" cx="1062" cy="1530" r="21"/>
        <circle class="badge" cx="1062" cy="1586" r="21"/>
        <text class="t-white t-web" x="1140" y="1500" text-anchor="middle" transform="rotate(-90 1140 1500)" font-size="10">WWW.WICKHAVEN.COM</text>
      </g>
    </g>

    <!-- back wall (upside down) -->
    <g class="back-wall">
      <rect class="panel" x="390" y="1645" width="705" height="223"/>
      <rect class="cut" x="390" y="1645" width="705" height="223"/>
      <line class="fold" x1="523" y1="1645" x2="523" y2="1868"/>
      <line class="fold" x1="962" y1="1645" x2="962" y2="1868"/>
      <g transform="rotate(180 742 1755)">
        <circle cx="742" cy="1700" r="11" fill="var(--ink-light)"/>
        <text class="t-white t-brand" x="742" y="1750" text-anchor="middle" font-size="40">Wick Haven</text>
        <text class="t-white t-tag" x="742" y="1764" text-anchor="middle">LUXURY HOMEMADE CANDLES</text>
      </g>
    </g>

    <!-- lid top -->
    <g class="lid">
      <path class="pattern-area" d="M360 1868 H1125 Q1175 1868 1175 1960 V2080 Q1175 2168 1125 2168 H360 Q310 2168 310 2080 V1960 Q310 1868 360 1868 Z" role="img" aria-label="Orange geometric lattice pattern with small candelabra motifs"/>
      <rect class="panel" x="648" y="1868" width="188" height="300"/>
      <path class="cut" d="M360 1868 H1125 Q1175 1868 1175 1960 V2080 Q1175 2168 1125 2168 H360 Q310 2168 310 2080 V1960 Q310 1868 360 1868 Z"/>
      <line class="fold" x1="523" y1="1868" x2="523" y2="2168"/>
      <line class="fold" x1="962" y1="1868" x2="962" y2="2168"/>
      <circle cx="744" cy="1920" r="8" fill="var(--ink-light)"/>
      <text class="t-white t-brand" x="742" y="1968" text-anchor="middle" font-size="28">Wick Haven</text>
      <text class="t-white t-tag" x="742" y="1980" text-anchor="middle" font-size="5.5">LUXURY HOMEMADE CANDLES</text>
      <text class="t-white t-title" x="742" y="2046" text-anchor="middle">CANDLE</text>
      <text class="t-white t-title" x="742" y="2070" text-anchor="middle">MAKING KIT</text>
      <text class="t-orange t-sub" x="742" y="2087" text-anchor="middle">WITH FRAGRANCES &amp; COLORS</text>
      <text class="t-white t-web" x="742" y="2148" text-anchor="middle">WWW.WICKHAVEN.COM</text>
    </g>

    <!-- front tuck flap -->
    <g class="front-flap">
      <path class="panel" d="M420 2178 Q390 2182 390 2240 V2300 Q390 2390 470 2390 H1015 Q1095 2390 1095 2300 V2240 Q1095 2182 1065 2178 Z"/>
      <path class="cut" d="M420 2178 Q390 2182 390 2240 V2300 Q390 2390 470 2390 H1015 Q1095 2390 1095 2300 V2240 Q1095 2182 1065 2178 Z"/>
      <line class="fold" x1="523" y1="2168" x2="523" y2="2390"/>
      <line class="fold" x1="962" y1="2168" x2="962" y2="2390"/>
      <circle cx="744" cy="2215" r="8" fill="var(--ink-light)"/>
      <text class="t-white t-brand" x="742" y="2262" text-anchor="middle" font-size="28">Wick Haven</text>
      <text class="t-white t-tag" x="742" y="2274" text-anchor="middle" font-size="5.5">LUXURY HOMEMADE CANDLES</text>
      <text class="t-white t-quote" x="742" y="2310" text-anchor="middle">When everything seemed dark I lit up a candle.</text>
      <text class="t-white t-quote" x="742" y="2330" text-anchor="middle">Hope this kit can help you lit up your path</text>
      <text class="t-white t-quote" x="742" y="2350" text-anchor="middle">to happiness.</text>
    </g>
  </svg>

</main>
</body>
</html>
```